Preisliste für Kosmetikinstitut
Zielgruppe
Ich benötige für mein Kosmetikinstitut eine Preisliste für die moderne Frau, aber auch Männer. Das Design sollte mein Logo enthalten. Farben des Designkonzepts einbauen.
A4 quer zum Falten, wie ein Heft, 1. Seite Preisliste mit logo, im Innenteil dann Anwendungen
Aufgabenstellung
Minimalistisch, ästhetisch, modern, edel
Kontaktdaten auf der Rückseite
LB Hautatelier
Lotte Brenner
Lindenhang 17
83671 Tannried
EMail: lotte@lb-hautatelier.de
Whatsapp: 0176 284 9017

```html
<!DOCTYPE html>
<html lang="de">
<head>
<meta charset="utf-8">
<title>Preisliste – LB Hautatelier</title>
<link href="https://fonts.googleapis.com/css2?family=Montserrat:wght@400;500;600&family=Marcellus&display=swap" rel="stylesheet">
<style>
  :root {
    --bg: #eceded;
    --paper: #f3f3f3;
    --band: #d9dadb;
    --band-light: #f8f8f8;
    --ink: #6f7578;
    --ink-strong: #5d6467;
    --ink-soft: #8b9093;
    --rule: #9aa0a3;
    --photo-gel: #dcdddd;
    --photo-skin: #cdbfb6;
    --photo-skin-2: #c9bcb4;
    --photo-flower: #e3e1df;
  }
  * { margin: 0; padding: 0; box-sizing: border-box; }
  html, body { width: 1200px; height: 900px; overflow: hidden; background: var(--bg); }
  body { position: relative; font-family: "Montserrat", sans-serif; color: var(--ink); }

  .page { position: absolute; background: var(--paper); box-shadow: 0 3px 6px rgba(0,0,0,.12); overflow: hidden; }
  .photo { position: absolute; }

  .cover { left: 220px; top: 53px; width: 241px; height: 377px; }
  .cover-texture { left: 72px; top: 0; width: 97px; height: 193px;
    background: linear-gradient(160deg, #e4e5e5, var(--photo-gel) 55%, #e1e2e2); }
  .brand { position: absolute; left: 0; width: 241px; top: 92px; text-align: center;
    font-size: 7px; font-weight: 500; letter-spacing: .12em; color: var(--ink-soft); }
  .brand-dot { display: inline-block; width: 5px; height: 5px; border-radius: 50%;
    background: var(--ink-soft); margin-right: 4px; vertical-align: 1px; }
  .cover-title { position: absolute; left: 0; width: 241px; top: 341px; text-align: center;
    font-family: "Marcellus", serif; font-size: 13px; letter-spacing: .18em; color: var(--ink); }

  .spread-page { height: 377px; }
  .edge-band { position: absolute; top: 0; bottom: 0; background: var(--band); }

  .col { position: absolute; }
  .section-title { font-size: 6.6px; font-weight: 500; letter-spacing: .06em; color: var(--ink-strong); }
  .section-rule { width: 20px; height: 1px; background: var(--rule); margin: 5px 0 8px; }
  .item { margin-bottom: 8px; }
  .item-head { display: flex; justify-content: space-between; font-size: 5.2px; font-weight: 600;
    letter-spacing: .04em; color: var(--ink-strong); line-height: 1.45; }
  .item-head .price { font-weight: 400; white-space: nowrap; margin-left: 6px; }
  .item-sub { font-weight: 400; }
  .item-text { font-size: 4.6px; line-height: 1.55; text-align: justify; margin-top: 3px; color: var(--ink); }
  .item-text.left { text-align: left; }
  .steps { list-style: none; font-size: 4.5px; line-height: 1.5; margin-top: 4px; }
  .steps li { display: flex; gap: 6px; margin-bottom: 2px; }
  .price-row { display: flex; justify-content: space-between; font-size: 4.8px; font-weight: 600;
    color: var(--ink-strong); line-height: 1.6; }
  .price-row span:last-child { font-weight: 400; }
  .extra-row { display: flex; justify-content: space-between; font-size: 5.2px; font-weight: 500;
    color: var(--ink-strong); line-height: 1.5; }
  .note { font-size: 4.2px; margin-top: 4px; line-height: 1.4; color: var(--ink-soft); }

  .contact { position: absolute; left: 62px; top: 308px; font-size: 5px; line-height: 1.6; color: var(--ink); }
  .contact .label { font-size: 4.2px; font-weight: 600; letter-spacing: .1em; }
  .contact .name { font-size: 6px; margin-bottom: 3px; }
  .contact-rule { position: absolute; left: 52px; top: 245px; width: 1px; height: 103px; background: var(--rule); }
</style>
</head>
<body>

<section class="page cover">
  <div class="photo cover-texture" role="img" aria-label="Transparente Gel-Textur mit Wassertropfen"></div>
  <div class="brand"><span class="brand-dot"></span>LB HAUTATELIER</div>
  <div class="cover-title">PREISLISTE</div>
</section>

<section class="page spread-page" style="left:498px; top:53px; width:243px;">
  <div class="edge-band" style="left:0; width:27px; background:var(--band-light);"></div>
  <div class="col" style="left:56px; top:96px; width:129px;">
    <div class="section-title">GESICHTSBEHANDLUNGEN</div>
    <div class="section-rule"></div>
    <div class="item">
      <div class="item-head"><span>EXPRESS FACIAL TREATMENT</span><span class="price">€ 59,00</span></div>
      <p class="item-text left">Für alle, die wenig Zeit haben und trotzdem ihre Haut auffrischen und revitalisieren wollen. Reinigung, Enzympeeling, Serum, Maske, Abschlusspflege; 35-45min</p>
    </div>
    <div class="item">
      <div class="item-head"><span>CLASSIC FACIAL TREATMENT<br>KLASSISCHE GESICHTSBEHANDLUNG</span><span class="price">€ 89,00</span></div>
      <p class="item-text left">Reinigung, Enzympeeling, Vapozon, Ausreinigung, Augenbrauenkorrektur, Ampulle, Maske, individuelle Abschlusspflege; 45-60min</p>
    </div>
    <div class="item">
      <div class="item-head"><span>CLEAR SKIN TREATMENT</span><span class="price">€ 89,00</span></div>
      <p class="item-text">Die Haut wirkt ausgeglichener, Unreinheiten wird vorgebeugt, der Teint erhält Balance und kann sich beruhigen. Gleichzeitig wird die Haut durch die Hyaluronsäure vitalisiert und Falten und Fältchen kann entgegengewirkt werden. 50-60min</p>
    </div>
    <div class="item">
      <div class="item-head"><span>CAPILARINE TREATMENT</span><span class="price">€ 89,00</span></div>
      <p class="item-text left">Hautrötungen und Couperose Erscheinungen werden gelindert, die Gefäßwände werden gestärkt und das Hautbild wirkt ausgeglichener, mögliche Irritationen gehen zurück. Gleichzeitig sorgt die hochkonzentrierte Hyaluronsäure für Frische, Vitalität und Glätte; 50-60min</p>
    </div>
  </div>
</section>
<section class="page spread-page" style="left:741px; top:53px; width:243px;">
  <div class="col" style="left:57px; top:92px; width:129px;">
    <div class="item">
      <div class="item-head"><span>SOLVIRA SOFT TREATMENT<br><span class="item-sub">(FÜR DIE EMPFINDLICHE, GEREIZTE HAUT)</span></span><span class="price">€ 79,00</span></div>
      <p class="item-text">Entzündliche Prozesse können gemildert werden, gereizte Haut oder solche, die wenig verträgt, wird beruhigt. Irritationen können zurückgehen, die Haut erhält Balance. ca 50min</p>
    </div>
    <div class="item">
      <div class="item-head"><span>VITAMIN SOFT BOOST</span><span class="price">€ 79,00</span></div>
      <p class="item-text">Vitamine sorgen für Power und Frische in und auf der Haut, die Widerstandskraft der Haut wird gestärkt. Die Faltentiefe kann gemildert werden. ca. 50min</p>
    </div>
    <div class="item">
      <div class="item-head"><span>ANTI-AGE ADVANCED</span><span class="price">€ 99,00</span></div>
      <p class="item-text">Die Haut wirkt insgesamt erfrischt, vitalisiert und gestrafft. Feine Linien und Fältchen werden reduziert. 50-70min (je nach Peeling)</p>
    </div>
    <div class="item">
      <div class="item-head"><span>CHEMISCHES PEELING<br>(OKTOBER – APRIL)</span><span class="price" style="align-self:flex-end">€ 89,00</span></div>
      <p class="item-text">Professionelle Peelings können viele Problemstellungen lindern, verbessern oder gar beheben. Dazu gehören die Zellerneuerung, Glättung der Hauttextur, Reduzierung von Pigmentflecken, Verbesserung von Akne.</p>
    </div>
  </div>
</section>
<div class="photo" style="left:705px; top:289px; width:70px; height:141px; background:linear-gradient(180deg,#bdb3ad,var(--photo-skin));" role="img" aria-label="Porträtfoto einer Frau mit gepflegter Haut"></div>
<div class="photo" style="left:778px; top:350px; width:69px; height:80px; background:linear-gradient(180deg,#c3c1c2,var(--photo-skin-2));" role="img" aria-label="Detailfoto von Händen am Gesicht"></div>

<section class="page spread-page" style="left:220px; top:470px; width:244px;">
  <div class="col" style="left:46px; top:46px; width:150px;">
    <div class="section-title">APPARATIVE BEHANDLUNGEN</div>
    <div class="section-rule"></div>
    <div class="item-head"><span>AQUAFINE –<br>„GLOWING SKIN“ TREATMENT</span><span class="price" style="align-self:flex-end">€ 140,00</span></div>
    <p class="item-text" style="margin-top:7px">In 6 Schritten zu einer Haut mit einmaligem Glow-Effekt:</p>
    <ol class="steps">
      <li><span>1.</span><span>Behandlungsschritt: die Haut wird tiefengereinigt</span></li>
      <li><span>2.</span><span>Behandlungsschritt: die obersten Verhornungen und Schuppen werden sanft mit einem Peeling gelöst</span></li>
      <li><span>3.</span><span>Behandlungsschritt: die Haut wird in der Tiefe gereinigt und entschlackt</span></li>
      <li><span>4.</span><span>Behandlungsschritt: niedermolekulare Wirkstoffe werden aufgebracht, um die Haut zu erfrischen und den entsprechenden Glow zu geben</span></li>
      <li><span>5.</span><span>Ausgewählte und hochdosierte Wirkstoffessenzen werden auf die Haut gesprüht und durch die niedrige Molekularstruktur können diese tiefer in der Haut wirken.</span></li>
      <li><span>6.</span><span>Zum Schluss werden die Essenzen durch eine Impulsgebende Druckluft-Massage noch tiefer in die Haut gebracht; 60min</span></li>
    </ol>
    <div class="item-head" style="margin-top:9px"><span>MIKRODERMABRASION</span></div>
    <p class="item-text">Bei der Mikrodermabrasion handelt es sich um ein mechanisches Hautpeeling, dabei werden mittels feinster Kristalle die Hornzellen der obersten Hautschicht schonend abgetragen und dann mit Hilfe eines Unterdrucks behutsam abgesaugt.</p>
    <p class="item-text">Der revitalisierende Prozess erhöht die Durchblutung, fördert die Zellerneuerung und verleiht Ihrer Haut ein zartes frisches Gefühl. Die Haut gewinnt an Spannkraft, feine Fältchen werden gemildert und Poren sichtbar verkleinert.</p>
    <p class="item-text">Außerdem hilft es bei oberflächlichen Akne Narben, Pigmentstörungen und Dehnungsstreifen. Wirkstoffe können nun wieder besser von der Haut aufgenommen werden.</p>
    <div style="margin-top:3px">
      <div class="price-row"><span>GESICHT</span><span>€ 89,00</span></div>
      <div class="price-row"><span>GESICHT, HALS, DEKOLLETÉ</span><span>€ 110,00</span></div>
    </div>
  </div>
</section>
<section class="page spread-page" style="left:464px; top:470px; width:243px;">
  <div class="edge-band" style="left:214px; width:29px;"></div>
  <div class="col" style="left:56px; top:66px; width:130px;">
    <div class="section-title" style="font-size:6px">MICRONEEDLING</div>
    <p class="item-text" style="margin-top:6px">Die Behandlung eignet sich besonders für Menschen, die ihre Hautqualität verbessern und Falten, (Akne)Narben, Pigmentverschiebungen, große Poren und sogar Haarausfall behandeln wollen.</p>
    <p class="item-text">Mit Hilfe feinster Nadeln werden der Haut kontrolliert Mikroverletzungen zugeführt, dies regt die natürliche Wundheilung, sowie Kollagen- und Elastin Bildung an. Microneedling ist also eine natürliche Beauty-Behandlung, die körpereigene Reparaturmechanismen nutzt, um ein strafferes Hautbild zu erhalten.</p>
    <p class="item-text">Bereits nach der ersten Behandlung sieht die Haut aufgepolstert, frisch und rosig aus. Kleine Linien und Fältchen werden tiefenbehandelt. Die Haut wirkt straffer und jugendlicher.</p>
    <p class="item-text">Ein weiterer Vorteil, durch die Stichkanäle können Wirkstoffe besser von der Haut aufgenommen werden.</p>
    <div style="margin-top:3px">
      <div class="price-row"><span>GESICHT</span><span>€ 110,00</span></div>
      <div class="price-row"><span>GESICHT, HALS</span><span>€ 130,00</span></div>
      <div class="price-row"><span>GESICHT, HALS, DEKOLLETÉ</span><span>€ 150,00</span></div>
    </div>
    <div class="section-title" style="margin-top:13px">ZUSATZLEISTUNGEN</div>
    <div class="section-rule"></div>
    <div class="extra-row"><span>Augenbrauen zupfen</span><span>€&nbsp;&nbsp;08,00</span></div>
    <div class="extra-row"><span>Augenbrauen färben</span><span>€&nbsp;&nbsp;12,00</span></div>
    <div class="extra-row"><span>Wimpern färben</span><span>€&nbsp;&nbsp;15,00</span></div>
    <div class="extra-row"><span>Enthaarung</span><span>€&nbsp;&nbsp;10,00-<br>€&nbsp;&nbsp;30,00</span></div>
    <p class="note">(Enthaarung der störenden Gesichts-<br>behaarung mittels Wax.)</p>
  </div>
</section>
<div class="photo" style="left:447px; top:523px; width:62px; height:104px; background:linear-gradient(180deg,#c9c5c3,var(--photo-skin));" role="img" aria-label="Profilfoto einer Frau mit Creme auf der Wange"></div>
<div class="photo" style="left:417px; top:607px; width:63px; height:39px; background:linear-gradient(135deg,#eeeeee,#dedede);" role="img" aria-label="Cremige weiße Textur"></div>

<section class="page" style="left:745px; top:470px; width:241px; height:377px;">
  <div class="photo" style="left:115px; top:33px; width:104px; height:185px; background:linear-gradient(120deg,#ebe9e7,var(--photo-flower) 60%,#d8d5d2);" role="img" aria-label="Hand hält eine Blume vor einem hellen Vorhang mit Schattenwurf"></div>
  <div class="contact-rule"></div>
  <div class="contact">
    <div class="label">LB HAUTATELIER</div>
    <div class="name">Lotte Brenner</div>
    <div>Lindenhang 17, 83671 Tannried</div>
    <div>E-Mail: lotte@lb-hautatelier.de</div>
    <div>Whatsapp: 0176 284 9017</div>
  </div>
</section>

</body>
</html>
```